Harrow Tavern & Grille Menu Makeover

I am looking for a professional look to update our current menu. We are an independently owned sports bar and grill. Up to this point, I have done all of my own graphic designing. I am looking for something classy/family oriented. We are a very family friendly sports bar that offers a wide variety of menu options. Our website is www.harrowtavernco.example. This may help you get more of a feel for what type of place we are and what we offer. Our menu is listed on the website. My current menu is 8.5x14 inserts that feature a cover page, 4 inside pages and a back page. I would like something a little more condensed than this. Possibly a large tri-fold menu? I am open to all new ideas. I do have some pictures on my menu now, and would like to continue using a few pictures to feature some of my items. I would like something that is in a format that gives me the option to change items and prices on my own in the future. I would also like it to feature, or inform my patrons about our technology that we offer. We offer online ordering and we are a "verified venue" with Brewvoke.( a social site for craft beer lovers).

Industry/Entity Type

Sports Bar

Requirements
Nice to have
• Nice to have some pictures, but does not have to. We do feature 9 different beers on tap. A lot of them are local craft beers from the state of Kansas. Not sure if that is something we can feature, but it is a nice talking point. All of our tables and bar are hand built. With a rich mahogany finish on all of our woodwork, some type of "woodgrain" look into the menu would be nice.

```html
<!DOCTYPE html>
<html lang="en">
<head>
<meta charset="utf-8">
<title>Harrow Tavern &amp; Grille — Sides</title>
<link rel="stylesheet" href="https://fonts.googleapis.com/css2?family=Playfair+Display+SC:wght@700&family=Oswald:wght@400&family=Syncopate:wght@700&display=swap">
<style>
  :root {
    --wood-dark: #4a1a0c;
    --wood-mid: #7a2e14;
    --wood-light: #8e3a1a;
    --paper-light: #e4d0ac;
    --paper-mid: #d6bb8e;
    --paper-edge: #b48d58;
    --ink: #1c1510;
    --note: #f4ece0;
  }
  * { margin: 0; padding: 0; box-sizing: border-box; }
  html, body { width: 850px; height: 1200px; overflow: hidden; }
  body { position: relative; background: var(--wood-dark); }

  .woodgrain {
    position: absolute; inset: 0;
    background: linear-gradient(90deg, var(--wood-dark) 0%, var(--wood-mid) 20%, var(--wood-light) 45%, var(--wood-mid) 70%, var(--wood-dark) 100%);
  }
  .parchment {
    position: absolute; left: 48px; top: 80px; width: 754px; height: 1018px;
    background: radial-gradient(ellipse at 50% 40%, var(--paper-light) 0%, var(--paper-mid) 65%, var(--paper-edge) 100%);
    box-shadow: 0 6px 18px rgba(0,0,0,0.5);
  }

  .menu-title {
    position: absolute; top: 250px; left: 0; width: 100%;
    text-align: center; color: var(--ink);
    font-family: "Playfair Display SC", serif; font-weight: 700; font-size: 44px;
  }

  .side-list {
    position: absolute; top: 352px; left: 0; width: 100%;
    list-style: none; text-align: center; color: var(--ink);
  }
  .side-item { height: 40px; }
  .side-name {
    display: block; font-family: "Oswald", sans-serif; font-size: 16px;
    line-height: 18px; transform: scaleX(0.85); letter-spacing: 0.2px;
  }
  .side-price {
    display: block; font-family: "Syncopate", sans-serif; font-weight: 700;
    font-size: 7px; line-height: 7px; letter-spacing: 0.5px;
  }

  .contact-bar {
    position: absolute; top: 1022px; left: 0; width: 100%;
    display: flex; justify-content: center; align-items: center; gap: 14px;
    font-family: "Syncopate", sans-serif; font-weight: 700; font-size: 8px;
    color: var(--ink); text-transform: uppercase; letter-spacing: 0.4px;
  }
  .contact-item { display: flex; align-items: center; gap: 12px; margin-right: 12px; }
  .contact-mark { width: 18px; height: 18px; background: var(--ink); display: block; }

  .policy-note {
    position: absolute; top: 1151px; left: 0; width: 100%; text-align: center;
    font-family: "Syncopate", sans-serif; font-weight: 700; font-size: 6.5px;
    color: var(--note); text-transform: uppercase; letter-spacing: 0.3px;
  }
</style>
</head>
<body>
  <div class="woodgrain" role="img" aria-label="Rich mahogany woodgrain tabletop background"></div>
  <div class="parchment" role="img" aria-label="Aged parchment sheet with torn edges"></div>

  <h1 class="menu-title">Sides</h1>

  <ul class="side-list">
    <li class="side-item"><span class="side-name">FRENCH FRIES</span><span class="side-price">2.00</span></li>
    <li class="side-item"><span class="side-name">MASHED POTATOES</span><span class="side-price">2.00</span></li>
    <li class="side-item"><span class="side-name">STEAMED VEGETABLES</span><span class="side-price">2.50</span></li>
    <li class="side-item"><span class="side-name">LOADED BAKED POTATO</span><span class="side-price">2.50</span></li>
    <li class="side-item"><span class="side-name">ONION RINGS</span><span class="side-price">2.00</span></li>
    <li class="side-item"><span class="side-name">FRUIT DISH</span><span class="side-price">2.00</span></li>
    <li class="side-item"><span class="side-name">COLE SLAW</span><span class="side-price">2.00</span></li>
    <li class="side-item"><span class="side-name">DINNER SALAD</span><span class="side-price">2.99</span></li>
    <li class="side-item"><span class="side-name">GRILLED SHRIMP SKEWER</span><span class="side-price">2.00</span></li>
    <li class="side-item"><span class="side-name">SWEET POTATO FRIES</span><span class="side-price">2.99</span></li>
    <li class="side-item"><span class="side-name">POTATO CHIPS</span><span class="side-price">2.00</span></li>
    <li class="side-item"><span class="side-name">COTTAGE CHEESE</span><span class="side-price">2.00</span></li>
    <li class="side-item"><span class="side-name">MACARONI &amp; CHEESE</span><span class="side-price">4.00</span></li>
  </ul>

  <div class="contact-bar">
    <span class="contact-item"><span class="contact-mark"></span>harrowtavernandgrille</span>
    <span class="contact-item"><span class="contact-mark"></span>harrowtavernco.example</span>
    <span class="contact-item"><span class="contact-mark"></span>Brewvoke</span>
  </div>

  <p class="policy-note">When splitting a large portion, you will be charged the price of a small portion if a small portion is offered</p>
</body>
</html>
```